Two Versions of a Business Card for a Lawyer

Summary: I need a logo and a business card. The business card is two-sided and comes in two versions. One version is conservative, the other is slightly different with one or more pink embellishments in the logo or somewhere else in the business card.
I'm about to start off as a sole practitioner in criminal and immigration law. I'll largely be working with marginalised communities and in areas of social justice. One of my main focuses will be gendered violence, I'm hoping to specialise my practice towards representing victims of domestic and sexual violence and sex workers. I want a business card which would attract this clientele and make them feel safe to speak with me. I'd also like it to communicate a sense of hope.
However, the business card still has to be very conservative as the legal profession is very stuffy. So I was thinking of having two versions of the same card, one would be very straight forward while the other would have a **pink embellishment** or perhaps several. For example, if the scales of justice were used in the design, maybe the second version would have a pink flower about to bloom on the scale somewhere. Or maybe it's my logo that is different and pink.
While both designs have to be pretty conservative, I still want it to give off a sense that I'm alternative and think outside the box. With lawyers, I think a little bit of deviation goes a long way (less is more).
As far as colour goes (other than the pink embellishment), I was thinking something monochromatic, probably black and white but I am open to considering more colours. I personally love colour, and would love to use more colour, but am hesitant because of the nature of the profession. If you can find a way to use more colour while keeping it conservative and letting the pink pop, I'd be pretty pleased.
In general, I would prefer a clean simplistic design and logo. It should be immediately obvious that I'm a lawyer just by glancing at the card. I'm open to symbols of law, like the scales of justice or lady justice or something else. However, I don't want it to be the same as everyone else's.
Eventually, the design/style should be easy to recreate in the form of a website.
As far as the logo goes, it would probably use a circle as my last name starts with the letter "O". It can be very simple, with just my name and "Barrister & Solicitor". I don't currently have a logo, but the winning designer will be invited to provide a separate file for just the logo for an additional fee (I think it was CA$99). (Please ignore the uploaded logo file, it just wouldn't let me continue without uploading something).
As for the information that should go into the card, I'm still finalizing my address and phone number. So please use a placeholder for now.
Target Market(s)
Women, victims of sexual or domestic violence, refugees, people in need of legal services
Industry/Entity Type
Lawyer
Contact Information for Business Card
Marla Vent
Barrister & Solicitor
LL.B., B.C.L., B.F.A.
Criminal & Immigration Law
Street address
Toronto, ON
Postal Code
Phone number
Fax number
Email
Logo Text
Marla Vent, Barrister & Solicitor
Requirements
Must have
- Two versions
- One with pink
- Simplistic
Nice to have
- Maybe more colour
Should not have
- Not too conservative
- Not too predictable

```html
<!DOCTYPE html>
<html lang="en">
<head>
<meta charset="utf-8">
<title>Marla Vent — Business Cards</title>
<link rel="stylesheet" href="https://fonts.googleapis.com/css2?family=Poiret+One&display=swap">
<style>
  :root {
    --backdrop: #ece9e4;
    --ink: #1a1a1a;
    --mustard: #e2c021;
    --paper: #ffffff;
    --pink: #e0489f;
    --band-dark: #111111;
  }
  * { margin: 0; padding: 0; box-sizing: border-box; }
  html, body {
    width: 1200px; height: 891px; overflow: hidden;
    background: var(--backdrop);
  }
  .stage {
    position: relative; width: 1200px; height: 891px;
    display: flex; justify-content: center; align-items: center; gap: 110px;
  }
  .card {
    position: relative; width: 340px; height: 590px;
    font-family: "Poiret One", sans-serif; color: var(--ink);
    box-shadow: 0 10px 30px rgba(0,0,0,0.18);
    overflow: hidden;
  }
  .card--classic { background: var(--mustard); }
  .card--pink { background: var(--paper); }
  .card__band {
    position: absolute; left: 0; right: 0; bottom: 0; height: 62px;
  }
  .card--classic .card__band { background: var(--band-dark); }
  .card--pink .card__band { background: var(--pink); }

  .card__mark {
    position: absolute; left: 46px; top: 56px;
    width: 64px; height: 64px; border-radius: 50%;
    border: 2px solid var(--ink);
  }
  .card__identity { position: absolute; left: 46px; top: 138px; width: 250px; }
  .card__name { font-size: 36px; font-weight: 400; letter-spacing: 0.5px; line-height: 1.1; }
  .card__rule { height: 2px; background: var(--ink); margin: 6px 0 6px; }
  .card--pink .card__rule { background: var(--pink); }
  .card__title { font-size: 21px; line-height: 1.15; }
  .card__credentials { font-size: 21px; line-height: 1.15; letter-spacing: 1px; }

  .card__contact {
    position: absolute; left: 46px; top: 300px; width: 270px;
    font-size: 18px; line-height: 1.35;
  }
  .contact__row { display: flex; white-space: nowrap; }
  .contact__label { width: 78px; flex: none; }
  .contact__indent { padding-left: 78px; }
</style>
</head>
<body>
<main class="stage">

  <article class="card card--classic" aria-label="Business card, classic version">
    <span class="card__mark" aria-hidden="true"></span>
    <div class="card__identity">
      <h1 class="card__name">Marla Vent</h1>
      <div class="card__rule"></div>
      <p class="card__title">Barrister &amp; Solicitor</p>
      <p class="card__credentials">LL.B. &nbsp;BCL. &nbsp;BFA.</p>
      <div class="card__rule"></div>
    </div>
    <div class="card__contact">
      <p class="contact__row"><span class="contact__label">Adresse:</span><span>Lorem ipsum dolor</span></p>
      <p class="contact__indent">iFuim deam duir</p>
      <p class="contact__row"><span class="contact__label">Email:</span><span>marlavent@mailbox.com</span></p>
      <p class="contact__row"><span class="contact__label">Fax:</span><span>00 00 00 00 00</span></p>
      <p class="contact__row"><span class="contact__label">Phone:</span><span>00 00 00 00 00 00</span></p>
    </div>
    <div class="card__band"></div>
  </article>

  <article class="card card--pink" aria-label="Business card, pink version">
    <span class="card__mark" aria-hidden="true"></span>
    <div class="card__identity">
      <h2 class="card__name">Marla Vent</h2>
      <div class="card__rule"></div>
      <p class="card__title">Barrister &amp; Solicitor</p>
      <p class="card__credentials">LL.B. &nbsp;BCL. &nbsp;BFA.</p>
      <div class="card__rule"></div>
    </div>
    <div class="card__contact">
      <p class="contact__row"><span class="contact__label">Adresse:</span><span>Lorem ipsum dolor</span></p>
      <p class="contact__indent">iFuim deam duir</p>
      <p class="contact__row"><span class="contact__label">Email:</span><span>marlavent@mailbox.com</span></p>
      <p class="contact__row"><span class="contact__label">Fax:</span><span>00 00 00 00 00</span></p>
      <p class="contact__row"><span class="contact__label">Phone:</span><span>00 00 00 00 00 00</span></p>
    </div>
    <div class="card__band"></div>
  </article>

</main>
</body>
</html>
```